Coffeeshop menu for filter tip

We want to have a cannabis (coffeeshop) menu in the size 25mm wide x 60mm wide. Some examples attached.

it must have the following text:
Menu

WEED p/g
Oblivane €16
Cloudplum €14
Tide Runner €14
Quincefig €16
Mega Marsh €14
Grey Heron €14

HASH p/g
Tashar Amber €12
Pebble Frost€11
Lime Dunes €14
Ash Petal €10

Target Market(s)

tourist in Amsterdam

Requirements
Nice to have
• cannabis sign leaf
• No Cigarettes allowed symbol

```html
<!DOCTYPE html>
<html lang="en">
<head>
<meta charset="utf-8">
<title>Coffeeshop Menu</title>
<link href="https://fonts.googleapis.com/css2?family=Questrial&display=swap" rel="stylesheet">
<style>
  :root {
    --bg: #0e0f0e;
    --panel: #000000;
    --yellow: #f7f03a;
    --white: #ffffff;
    --grey: #9c9c9c;
    --leaf-tone: #1e211e;
    --skyline: #050505;
  }
  html, body {
    margin: 0;
    padding: 0;
    width: 1200px;
    height: 2880px;
    overflow: hidden;
    background: var(--bg);
  }
  .menu-card {
    position: relative;
    width: 1200px;
    height: 2880px;
    background: var(--bg);
    font-family: "Questrial", "Century Gothic", sans-serif;
    overflow: hidden;
  }
  .leaf-backdrop {
    position: absolute;
    inset: 0 0 224px 0;
    background:
      radial-gradient(ellipse 520px 420px at 1000px 180px, rgba(60,64,58,0.35), transparent 70%),
      radial-gradient(ellipse 360px 700px at 40px 1250px, rgba(60,64,58,0.35), transparent 70%),
      radial-gradient(ellipse 420px 520px at 1150px 1450px, rgba(60,64,58,0.3), transparent 70%),
      radial-gradient(ellipse 700px 520px at 600px 2150px, rgba(50,54,50,0.35), transparent 70%),
      linear-gradient(180deg, #0c0d0c 0%, #161816 60%, #1b1d1b 100%);
  }
  .no-smoking {
    position: absolute;
    top: 62px;
    left: 0;
    width: 1200px;
    display: flex;
    justify-content: center;
    align-items: center;
    gap: 18px;
    color: var(--white);
    font-size: 38px;
    letter-spacing: 0.3em;
  }
  .no-smoking svg { width: 46px; height: 46px; }
  .panel-shape {
    position: absolute;
    left: 0;
    top: 0;
    width: 1200px;
    height: 2880px;
  }
  .section-title {
    position: absolute;
    display: flex;
    justify-content: space-between;
    color: var(--yellow);
    font-size: 122px;
    line-height: 1;
  }
  .weed-title { left: 152px; top: 232px; width: 670px; }
  .hash-title { left: 412px; top: 1600px; width: 640px; }
  .unit {
    position: absolute;
    color: var(--grey);
    font-size: 62px;
    line-height: 1;
  }
  .weed-unit { left: 938px; top: 318px; }
  .hash-unit { left: 166px; top: 1683px; }
  .price-list {
    position: absolute;
    margin: 0;
    padding: 0;
    list-style: none;
  }
  .price-list li {
    display: flex;
    align-items: center;
    height: 164.5px;
  }
  .item-name {
    color: var(--yellow);
    font-size: 68px;
    letter-spacing: 0.22em;
    text-transform: uppercase;
    white-space: nowrap;
  }
  .item-price {
    color: var(--white);
    font-size: 78px;
    letter-spacing: -0.04em;
  }
  .weed-list { left: 171px; top: 430px; width: 876px; }
  .weed-list li { justify-content: space-between; }
  .hash-list { left: 140px; top: 1785px; width: 930px; }
  .hash-list .item-price { width: 135px; text-align: right; margin-right: 68px; }
  .skyline {
    position: absolute;
    left: 0;
    top: 2470px;
    width: 1200px;
    height: 186px;
    background: linear-gradient(180deg, rgba(5,5,5,0) 0%, rgba(5,5,5,0.75) 45%, var(--skyline) 100%);
  }
  .footer-band {
    position: absolute;
    left: 0;
    top: 2656px;
    width: 1200px;
    height: 224px;
    background: var(--panel);
  }
  .footer-title {
    position: absolute;
    left: 245px;
    top: 2700px;
    width: 712px;
    display: flex;
    justify-content: space-between;
    color: var(--white);
    font-size: 150px;
    line-height: 1;
  }
</style>
</head>
<body>
<div class="menu-card">
  <div class="leaf-backdrop" role="img" aria-label="Faint cannabis leaf shapes scattered over a dark background"></div>

  <div class="no-smoking">
    <span>NO CIGARETTES</span>
    <svg viewBox="0 0 46 46" aria-hidden="true">
      <circle cx="23" cy="23" r="19" fill="none" stroke="#ffffff" stroke-width="3.5"/>
      <rect x="10" y="21" width="22" height="6" fill="#ffffff"/>
      <rect x="33" y="21" width="3" height="6" fill="#ffffff"/>
      <line x1="10" y1="10" x2="36" y2="36" stroke="#ffffff" stroke-width="3.5"/>
    </svg>
  </div>

  <svg class="panel-shape" viewBox="0 0 1200 2880" aria-hidden="true">
    <polygon points="864,248 1101,248 1101,1456 101,1456 101,371 864,371" fill="#000000"/>
    <polygon points="101,1611 248,1611 368,1733 1101,1733 1101,2475 101,2475" fill="#000000"/>
  </svg>

  <div class="section-title weed-title"><span>W</span><span>E</span><span>E</span><span>D</span></div>
  <div class="unit weed-unit">p/g</div>
  <ul class="price-list weed-list">
    <li><span class="item-name">Oblivane</span><span class="item-price">€16</span></li>
    <li><span class="item-name">Cloudplum</span><span class="item-price">€14</span></li>
    <li><span class="item-name">Tide Runner</span><span class="item-price">€14</span></li>
    <li><span class="item-name">Quincefig</span><span class="item-price">€16</span></li>
    <li><span class="item-name">Mega Marsh</span><span class="item-price">€14</span></li>
    <li><span class="item-name">Grey Heron</span><span class="item-price">€14</span></li>
  </ul>

  <div class="unit hash-unit">p/g</div>
  <div class="section-title hash-title"><span>H</span><span>A</span><span>S</span><span>H</span></div>
  <ul class="price-list hash-list">
    <li><span class="item-price">€12</span><span class="item-name">Tashar Amber</span></li>
    <li><span class="item-price">€11</span><span class="item-name">Pebble Frost</span></li>
    <li><span class="item-price">€14</span><span class="item-name">Lime Dunes</span></li>
    <li><span class="item-price">€10</span><span class="item-name">Ash Petal</span></li>
  </ul>

  <div class="skyline" role="img" aria-label="Silhouette of the Amsterdam city skyline"></div>
  <div class="footer-band"></div>
  <div class="footer-title"><span>M</span><span>E</span><span>N</span><span>U</span></div>
</div>
</body>
</html>
```